Online Dating Website called WinkAtWheel.com

PLEASE CAN ALL PARTICIPATING DESIGNERS PLEASE SUBMIT ALL PAGES AS DETAILED IN THE ORIGINAL BRIEF BELOW WITHIN 48 HOURS TO AVOID WINKATWHEEL EXTENDING THE CONTEST FURTHER.

We have an online dating website that is 95% fully functional and now require an exciting and creative designer to help us create the best dating experience. We are looking for your ideas on a couple of our key pages. These are our landing, profile and search page. We already have a homepage that we are happy with and winning designers will look to build upon the foundations of the homepage and extend them through their designs.

The premise of the site is the idea that if you've ever seen someone out driving and wished you could communicate because you found them attractive, how would you? Well with WinkAtWheel.com you can. Just enter their vehicle registration number (license plate) in to the website in order to get in touch, flirt and develop a relationship. It also allows users to find each other based on other criteria. It acts as both a specialist service and a normal dating website.

The pages that require developing are 1) our landing page, this is the page users see when they first login to the site, it comprises various pieces of information but it's primary function is a live feed of events generated based on the users favourited profiles and interactions with the user. 2) The profile page is the page where users can edit their own information, given the nature of this page we are looking for a creative design that gives this page some flair. 3) Finally we are looking for ideas for our search page, this page needs to provide a list of users who meet the user's search requirements and display the profile of a selected user.
Updates

Project Deadline Extended
Reason: We've asked for certain pages in our brief to be designed and this still hasn't been done. We've contacted the designers that have currently submitted designs and requested this several times. We still await for this to happen.

Target Market(s)

Male or Female age 18+

Industry/Entity Type

Dating

Requirements
Must have
• Our must have feature is a designer with an open mind. The functionality of the site must be present, all we ask is for you to be creative with the layout. Think out side of the box, change the colours, the layout, and the background as you feel. Make it look current and appealing to the user.
Nice to have
• Theme's carried through from the home page
Should not have
• Do not include Comic Sans or Times New Roman font in your designs.

```html
<!DOCTYPE html>
<html lang="en">
<head>
<meta charset="utf-8">
<title>WinkAtWheel – Search</title>
<link href="https://fonts.googleapis.com/css2?family=Open+Sans:wght@400;600;700&display=swap" rel="stylesheet">
<style>
:root{
  --pink:#ec4e9a;
  --pink-dark:#d63c86;
  --blue:#2b8fdc;
  --ink:#333;
  --muted:#777;
  --faint:#999;
  --line:#e2e2e2;
  --panel:#fff;
  --head:#1a0a24;
  --chat:#2f8ee8;
}
*{box-sizing:border-box;margin:0;padding:0}
html,body{width:1076px;height:1200px;overflow:hidden}
body{
  font-family:"Open Sans",Arial,sans-serif;color:var(--ink);
  background:
    radial-gradient(ellipse 420px 160px at 880px 620px,rgba(255,60,160,.55),transparent 70%),
    radial-gradient(ellipse 500px 140px at 220px 180px,rgba(255,70,170,.35),transparent 70%),
    radial-gradient(ellipse 300px 300px at 950px 1000px,rgba(240,40,120,.45),transparent 70%),
    linear-gradient(160deg,#2a0a3a 0%,#4a0e4e 40%,#3a0832 70%,#1d0526 100%);
}
.stage{position:absolute;left:0;top:0;width:1000px;height:1115px;transform:scale(1.076);transform-origin:0 0}
.abs{position:absolute}

/* header */
.site-header{left:0;top:0;width:1000px;height:56px;background:rgba(20,6,28,.92);border-bottom:1px solid #3a2244}
.brand{left:24px;top:12px;display:flex;align-items:center;gap:8px;color:#fff;font-size:29px;font-weight:400;letter-spacing:-.3px}
.brand-dot{width:22px;height:22px;border-radius:50%;background:var(--pink)}
.main-nav{right:22px;top:20px;display:flex;gap:0;font-size:13px}
.main-nav a{color:#a9a2b0;text-decoration:none;margin-left:32px}
.main-nav .support{color:#3aa6ee;display:flex;align-items:center;gap:5px;margin-left:28px}
.main-nav .account{color:var(--pink);display:flex;align-items:center;gap:5px;margin-left:18px}

/* main panel */
.panel{left:23px;top:81px;width:827px;height:969px;background:var(--panel);overflow:hidden}
.divider{left:346px;top:0;width:5px;height:969px;border-left:1px solid var(--line);border-right:1px solid var(--line)}

.sidebar{left:18px;top:0;width:279px}
.side-title{color:var(--blue);font-size:14px;font-weight:600;padding:16px 0 10px;border-bottom:1px solid var(--line)}
.setting{display:flex;justify-content:space-between;font-size:11.5px;height:26px;align-items:center}
.setting b{font-weight:700;color:#444}
.setting span{color:var(--faint)}
.settings-list{padding-top:8px}
.tool-bar{margin-top:8px;background:#f1f1f1;height:32px;display:flex;align-items:center;font-size:11px;color:#555}
.tool-bar div{display:flex;align-items:center;gap:5px;padding:0 8px;border-right:1px solid #ddd}
.tool-bar div:last-child{border:0}
.results-title{margin-top:5px}

.results{margin-top:11px}
.result{position:relative;height:140px;border-top:2px solid var(--pink);background:linear-gradient(#f0f0f0 0,#fff 50px)}
.avatar{position:absolute;left:14px;top:15px;width:48px;height:48px;background:linear-gradient(135deg,#8a6a52,#c9a488 60%,#6b5040)}
.r-name{position:absolute;left:71px;top:15px;font-size:13.5px;font-weight:700;color:#222}
.r-meta{position:absolute;left:71px;top:35px;font-size:10px;color:var(--faint)}
.r-icons{position:absolute;left:72px;top:51px;display:flex;gap:5px}
.r-text{position:absolute;left:14px;top:71px;width:265px;font-size:11px;line-height:18px;color:#555}

/* timeline */
.t-heart{width:46px;height:46px}
.card{left:385px;width:410px;border:1px solid #d8d8d8;background:#fff}
.card::before{content:"";position:absolute;left:-7px;top:10px;width:12px;height:12px;background:#fff;border-left:1px solid #d8d8d8;border-bottom:1px solid #d8d8d8;transform:rotate(45deg)}
.card h3{color:var(--blue);font-size:13.5px;font-weight:600;padding:15px 19px 0}
.quote{font-size:13.5px;color:#555;padding:10px 19px 0}
.body{font-size:11.2px;line-height:18.3px;color:#555;padding:10px 18px 0 18px}
.body p{margin-bottom:18px}
.body p.tight{margin-bottom:0}
.body b{color:var(--pink);font-weight:600}
.like{position:absolute;width:22px;height:18px;background:#eee;border:1px solid #ddd;display:flex;align-items:center;justify-content:center}

/* profile card */
.profile{left:840px;top:91px;width:137px;height:739px;background:#fff;box-shadow:0 0 6px rgba(0,0,0,.3)}
.p-head{position:absolute;left:0;top:0;width:137px;height:297px;background:var(--pink)}
.p-photo{position:absolute;left:8px;top:9px;width:120px;height:132px;background:linear-gradient(180deg,#fafafa,#e6e6e6)}
.p-name{position:absolute;left:9px;top:149px;color:#fff;font-weight:700;font-size:14.5px}
.p-line{position:absolute;left:9px;color:#fff;font-size:10.5px;font-weight:600}
.p-btn{position:absolute;left:8px;width:120px;height:23px;background:#f3f3f3;color:#888;font-size:11px;font-weight:600;display:flex;align-items:center;gap:8px;padding-left:9px;letter-spacing:.4px}
.p-sec{position:absolute;left:9px;width:119px}
.p-sec h4{color:#3aa6ee;font-size:12.5px;font-weight:400;margin-bottom:5px}
.p-sec li{list-style:none;font-size:11px;line-height:22px;color:#555}
.p-sec li b{font-weight:700;color:#333}
.p-rule{position:absolute;left:9px;width:119px;border-top:1px solid #ddd}
.opt{font-size:11px;font-weight:600;color:#444;line-height:22px;display:flex;gap:5px;align-items:center}
.qm{position:absolute;left:9px;top:657px;width:119px;height:69px;border:1px solid #ddd;font-size:11px;color:#666;padding:4px 8px;line-height:14px}

.open-chat{left:868px;top:1085px;width:109px;height:30px;background:var(--chat);color:#fff;font-size:11px;font-weight:700;display:flex;align-items:center;justify-content:center;gap:7px;border-radius:3px 3px 0 0}
</style>
</head>
<body>
<div class="stage">

<header class="site-header abs">
  <div class="brand abs"><span>winkatwheel</span><span class="brand-dot"></span></div>
  <nav class="main-nav abs">
    <a>Home</a><a>Profile</a><a>Message</a><a>Matches</a><a>Search</a>
    <a class="support"><svg width="14" height="14" viewBox="0 0 14 14"><path d="M2 8V6a5 5 0 0 1 10 0v2" fill="none" stroke="#3aa6ee" stroke-width="1.6"/><rect x="1" y="7" width="3" height="4" rx="1" fill="#3aa6ee"/><rect x="10" y="7" width="3" height="4" rx="1" fill="#3aa6ee"/></svg>Support</a>
    <a class="account"><svg width="12" height="13" viewBox="0 0 12 13"><circle cx="6" cy="3.5" r="3" fill="#ec4e9a"/><path d="M0 13a6 5 0 0 1 12 0z" fill="#ec4e9a"/></svg>My Account</a>
  </nav>
</header>

<main class="panel abs">
  <aside class="sidebar abs">
    <h2 class="side-title">Search Settings</h2>
    <div class="settings-list">
      <div class="setting"><b>Looking for:</b><span>Brown</span></div>
      <div class="setting"><b>Minimum Age:</b><span>18</span></div>
      <div class="setting"><b>Maximum Age:</b><span>99</span></div>
      <div class="setting"><b>Distance:</b><span>Any Distance</span></div>
    </div>
    <div class="tool-bar">
      <div><svg width="12" height="12" viewBox="0 0 12 12"><rect x="1" y="2" width="4" height="9" rx="1" fill="#ec4e9a"/><rect x="7" y="2" width="4" height="9" rx="1" fill="#ec4e9a"/></svg>Any Distance</div>
      <div><svg width="12" height="12" viewBox="0 0 12 12"><circle cx="5" cy="5" r="3.5" fill="none" stroke="#ec4e9a" stroke-width="1.8"/><path d="M7.5 7.5L11 11" stroke="#ec4e9a" stroke-width="2"/></svg>Search Reg</div>
      <div><svg width="12" height="12" viewBox="0 0 12 12"><path d="M6 .5l1.7 3.6 3.8.4-2.9 2.6.9 3.9L6 9l-3.5 2 .9-3.9L.5 4.5l3.8-.4z" fill="#ec4e9a"/></svg>Favourites</div>
    </div>
    <h2 class="side-title results-title">My Results</h2>
    <div class="results">
      <article class="result"><div class="avatar" role="img" aria-label="Member profile photo"></div><div class="r-name">Stupid Llama</div><div class="r-meta">24 years old - from castleford</div><div class="r-icons"><svg width="50" height="9" viewBox="0 0 50 9"><path d="M4.5 8.5L1 5a2 2 0 0 1 3.5-3 2 2 0 0 1 3.5 3z" fill="#666"/><circle cx="17" cy="2.5" r="2.2" fill="#666"/><path d="M13 9a4 4 0 0 1 8 0z" fill="#666"/><rect x="27" y="0" width="6" height="9" rx="1" fill="#666"/><circle cx="43" cy="4.5" r="3.8" fill="none" stroke="#666" stroke-width="1.2"/></svg></div><p class="r-text">This is Pixelforge's version &nbsp;of Lorem Ipsum. Proin gravida nibh vel velit auctor aliquet. Aenean sollicitudin.</p></article>
      <article class="result"><div class="avatar" role="img" aria-label="Member profile photo"></div><div class="r-name">Stupid Llama</div><div class="r-meta">24 years old - from castleford</div><div class="r-icons"><svg width="50" height="9" viewBox="0 0 50 9"><path d="M4.5 8.5L1 5a2 2 0 0 1 3.5-3 2 2 0 0 1 3.5 3z" fill="#666"/><circle cx="17" cy="2.5" r="2.2" fill="#666"/><path d="M13 9a4 4 0 0 1 8 0z" fill="#666"/><rect x="27" y="0" width="6" height="9" rx="1" fill="#666"/><circle cx="43" cy="4.5" r="3.8" fill="none" stroke="#666" stroke-width="1.2"/></svg></div><p class="r-text">This is Pixelforge's version &nbsp;of Lorem Ipsum. Proin gravida nibh vel velit auctor aliquet. Aenean sollicitudin.</p></article>
      <article class="result"><div class="avatar" role="img" aria-label="Member profile photo"></div><div class="r-name">Stupid Llama</div><div class="r-meta">24 years old - from castleford</div><div class="r-icons"><svg width="50" height="9" viewBox="0 0 50 9"><path d="M4.5 8.5L1 5a2 2 0 0 1 3.5-3 2 2 0 0 1 3.5 3z" fill="#666"/><circle cx="17" cy="2.5" r="2.2" fill="#666"/><path d="M13 9a4 4 0 0 1 8 0z" fill="#666"/><rect x="27" y="0" width="6" height="9" rx="1" fill="#666"/><circle cx="43" cy="4.5" r="3.8" fill="none" stroke="#666" stroke-width="1.2"/></svg></div><p class="r-text">This is Pixelforge's version &nbsp;of Lorem Ipsum. Proin gravida nibh vel velit auctor aliquet. Aenean sollicitudin.</p></article>
      <article class="result"><div class="avatar" role="img" aria-label="Member profile photo"></div><div class="r-name">Stupid Llama</div><div class="r-meta">24 years old - from castleford</div><div class="r-icons"><svg width="50" height="9" viewBox="0 0 50 9"><path d="M4.5 8.5L1 5a2 2 0 0 1 3.5-3 2 2 0 0 1 3.5 3z" fill="#666"/><circle cx="17" cy="2.5" r="2.2" fill="#666"/><path d="M13 9a4 4 0 0 1 8 0z" fill="#666"/><rect x="27" y="0" width="6" height="9" rx="1" fill="#666"/><circle cx="43" cy="4.5" r="3.8" fill="none" stroke="#666" stroke-width="1.2"/></svg></div><p class="r-text">This is Pixelforge's version &nbsp;of Lorem Ipsum. Proin gravida nibh vel velit auctor aliquet. Aenean sollicitudin.</p></article>
      <article class="result"><div class="avatar" role="img" aria-label="Member profile photo"></div><div class="r-name">Stupid Llama</div><div class="r-meta">24 years old - from castleford</div><div class="r-icons"><svg width="50" height="9" viewBox="0 0 50 9"><path d="M4.5 8.5L1 5a2 2 0 0 1 3.5-3 2 2 0 0 1 3.5 3z" fill="#666"/><circle cx="17" cy="2.5" r="2.2" fill="#666"/><path d="M13 9a4 4 0 0 1 8 0z" fill="#666"/><rect x="27" y="0" width="6" height="9" rx="1" fill="#666"/><circle cx="43" cy="4.5" r="3.8" fill="none" stroke="#666" stroke-width="1.2"/></svg></div><p class="r-text">This is Pixelforge's version &nbsp;of Lorem Ipsum. Proin gravida nibh vel velit auctor aliquet. Aenean sollicitudin.</p></article>
    </div>
  </aside>

  <div class="divider abs"></div>

  <svg class="t-heart abs" style="left:324px;top:39px" viewBox="0 0 46 46"><path d="M23 44L5 24A11 11 0 0 1 23 9a11 11 0 0 1 18 15z" fill="#ec4e9a" stroke="#fff" stroke-width="2"/><path d="M15 15h16v10H21l-4 3v-3h-2z" fill="#fff"/></svg>
  <svg class="t-heart abs" style="left:324px;top:136px" viewBox="0 0 46 46"><path d="M23 44L5 24A11 11 0 0 1 23 9a11 11 0 0 1 18 15z" fill="#ec4e9a" stroke="#fff" stroke-width="2"/><path d="M15 24l2-6h12l2 6v4H15z" fill="none" stroke="#fff" stroke-width="2"/><circle cx="18.5" cy="25" r="1.3" fill="#fff"/><circle cx="27.5" cy="25" r="1.3" fill="#fff"/></svg>
  <svg class="t-heart abs" style="left:324px;top:246px" viewBox="0 0 46 46"><path d="M23 44L5 24A11 11 0 0 1 23 9a11 11 0 0 1 18 15z" fill="#ec4e9a" stroke="#fff" stroke-width="2"/><rect x="16" y="14" width="11" height="14" fill="#fff"/><rect x="20" y="17" width="11" height="14" fill="#fff" stroke="#ec4e9a"/><path d="M22 21h7M22 24h7M22 27h7" stroke="#ec4e9a"/></svg>
  <svg class="t-heart abs" style="left:324px;top:398px" viewBox="0 0 46 46"><path d="M23 44L5 24A11 11 0 0 1 23 9a11 11 0 0 1 18 15z" fill="#ec4e9a" stroke="#fff" stroke-width="2"/><circle cx="23" cy="21" r="7.5" fill="#fff"/><circle cx="20.5" cy="19.5" r="1" fill="#ec4e9a"/><circle cx="25.5" cy="19.5" r="1" fill="#ec4e9a"/><path d="M19.5 22.5a4 4 0 0 0 7 0" stroke="#ec4e9a" stroke-width="1.3" fill="none"/></svg>

  <section class="card abs" style="top:38px;height:77px">
    <h3>My Status</h3>
    <p class="quote">“ok”</p>
  </section>

  <section class="card abs" style="top:135px;height:78px">
    <h3>My Car</h3>
    <p class="quote">“I drive a Velora - Something in Blue.”</p>
  </section>

  <section class="card abs" style="top:245px;height:131px">
    <h3>My Bio</h3>
    <p class="body" style="line-height:18.5px">Lorem ipsum dolor sit amet, consectetur adipisicing elit, sed do eiusmod tempor incididunt ut labore et dolore magna aliqua. Ut enim ad minim veniam, quis nostrud exercitation ullamco laboris nisi ut aliquip ex ea commodo consequat.</p>
  </section>

  <section class="card abs" style="top:397px;height:500px">
    <h3>My Lifestyle</h3>
    <div class="body">
      <p><b>MOVIES:</b> Lorem Ipsum is simply dummy text of the printing and typesetting industry. Lorem Ipsum has been the industry's standard dummy text ever since the 1500s</p>
      <p><b>TV:</b> Lorem Ipsum is simply dummy text of the printing and typesetting industry. Lorem Ipsum has been the industry's standard dummy text ever since the 1500s, when an unknown printer took a galley of type and scrambled it to make a type specimen book. It has survived not only five centuries, but also the leap into electronic typesetting, remaining essentially unchanged.</p>
      <p><b>MUSIC:</b> Lorem Ipsum is simply dummy text of the printing and typesetting industry</p>
      <p class="tight"><b>PETS:</b> Lorem Ipsum is simply dummy text of the printing</p>
      <p><b>LANGUAGES:</b> Lorem Ipsum is simply dummy text</p>
      <p><b>INTERESTS:</b> Lorem Ipsum is simply dummy text of the printing and typesetting industry. Lorem Ipsum has been the industry's standard dummy text ever since the 1500s, when an unknown printer.</p>
      <p><b>HOBBIES:</b> Lorem Ipsum is simply dummy text of the printing and typesetting industry. Lorem Ipsum has been the industry's standard dummy text ever.</p>
    </div>
  </section>

  <div class="like" style="left:526px;top:280px"><svg width="10" height="9" viewBox="0 0 10 9"><path d="M5 9L1 5a2.3 2.3 0 0 1 4-3 2.3 2.3 0 0 1 4 3z" fill="#bbb"/></svg></div>
  <div class="like" style="left:526px;top:420px"><svg width="10" height="9" viewBox="0 0 10 9"><path d="M5 9L1 5a2.3 2.3 0 0 1 4-3 2.3 2.3 0 0 1 4 3z" fill="#bbb"/></svg></div>
  <div class="like" style="left:526px;top:560px"><svg width="10" height="9" viewBox="0 0 10 9"><path d="M5 9L1 5a2.3 2.3 0 0 1 4-3 2.3 2.3 0 0 1 4 3z" fill="#bbb"/></svg></div>
  <div class="like" style="left:526px;top:700px"><svg width="10" height="9" viewBox="0 0 10 9"><path d="M5 9L1 5a2.3 2.3 0 0 1 4-3 2.3 2.3 0 0 1 4 3z" fill="#bbb"/></svg></div>
  <div class="like" style="left:526px;top:840px"><svg width="10" height="9" viewBox="0 0 10 9"><path d="M5 9L1 5a2.3 2.3 0 0 1 4-3 2.3 2.3 0 0 1 4 3z" fill="#bbb"/></svg></div>
</main>

<aside class="profile abs">
  <div class="p-head">
    <div class="p-photo" role="img" aria-label="Profile photo of a road bicycle"></div>
    <div class="p-name">Rowan</div>
    <div class="p-line" style="top:172px">Age: 33 years old</div>
    <div class="p-line" style="top:188px">From: Wakefield</div>
    <div class="p-btn" style="top:210px"><svg width="13" height="10" viewBox="0 0 13 10"><rect x=".5" y="2" width="12" height="8" rx="1" fill="#ec4e9a"/><circle cx="6.5" cy="6" r="2.2" fill="#f3f3f3"/><rect x="4" y="0" width="5" height="3" fill="#ec4e9a"/></svg>PROFILE</div>
    <div class="p-btn" style="top:238px"><svg width="13" height="11" viewBox="0 0 13 11"><path d="M6.5 0l5 5H8.5v6h-4V5h-3z" fill="#ec4e9a"/></svg>GALLERY</div>
    <div class="p-btn" style="top:265px"><svg width="13" height="11" viewBox="0 0 13 11"><path d="M1 4h9l-2-2.5M12 7H3l2 2.5" fill="none" stroke="#ec4e9a" stroke-width="1.8"/></svg>ACTIVITY</div>
  </div>
  <div class="p-sec" style="top:309px">
    <h4>About Me</h4>
    <ul>
      <li><b>Eye:</b> Brown</li><li><b>Hair:</b> Black</li><li><b>Height:</b> 4’3”</li><li><b>Body:</b> Average</li>
      <li><b>Education:</b> University</li><li><b>Children:</b> No children</li><li><b>Smoking:</b> Sometimes</li><li><b>Drinking:</b> Often</li>
    </ul>
  </div>
  <div class="p-rule" style="top:516px"></div>
  <div class="p-sec" style="top:526px">
    <h4>Options</h4>
    <div class="opt" style="padding-left:18px">Unfavourite rowan</div>
    <div class="opt"><svg width="12" height="11" viewBox="0 0 12 11"><path d="M0 0h12v8H5l-3 3V8H0z" fill="#ec4e9a"/></svg>Chat with Rowan</div>
    <div class="opt"><svg width="12" height="12" viewBox="0 0 12 12"><circle cx="5" cy="5" r="3.5" fill="none" stroke="#ec4e9a" stroke-width="1.6"/><path d="M7.5 7.5L11 11" stroke="#ec4e9a" stroke-width="1.8"/></svg>Go to Search</div>
  </div>
  <div class="p-rule" style="top:621px"></div>
  <div class="p-sec" style="top:631px"><h4>Quick Message</h4></div>
  <div class="qm">Type a message to Rowan</div>
</aside>

<div class="open-chat abs"><svg width="15" height="13" viewBox="0 0 15 13"><path d="M0 0h10v7H4l-3 3V7H0z" fill="#fff"/><path d="M11 3h4v7h-1v3l-3-3H5V8h6z" fill="#fff"/></svg>OPEN CHAT</div>

</div>
</body>
</html>
```